Rosko Tamblin

I am a songwriter and would like to include a bio, pictures, discography, CD covers and access to some of my music

Target Market(s)

Music Lovers, songwriters publishers

Coding

Coded - Design and coding required

Number of Pages Required

5+ page

Requirements
Must have
• Pictures of my CD covers, pictures of me and either my Music or links to my music
Nice to have
Should not have
• cartoons

```html
<!DOCTYPE html>
<html lang="en">
<head>
<meta charset="utf-8">
<title>Rosko Tamblin — Songwriter</title>
<link href="https://fonts.googleapis.com/css2?family=Cormorant+Garamond:wght@600;700&family=Source+Sans+3:wght@400;600&display=swap" rel="stylesheet">
<style>
  :root{
    --slate:#6b7590;
    --slate-light:#8a93ab;
    --black:#000;
    --footer:#1a1a1a;
    --white:#fff;
    --nav-text:#555c6e;
    --serif:"Cormorant Garamond", Georgia, serif;
    --sans:"Source Sans 3", Arial, sans-serif;
  }
  *{box-sizing:border-box;margin:0;padding:0}
  html,body{width:1200px;height:4408px;overflow:hidden}
  body{position:relative;background:var(--black);color:var(--white);font-family:var(--sans)}
  .abs{position:absolute}

  /* header */
  .site-header{left:0;top:0;width:1200px;height:108px;background:var(--white)}
  .brand{font-family:var(--serif);font-weight:700;color:var(--slate);font-size:34px;line-height:1;display:flex;align-items:center;gap:10px}
  .brand-dot{width:14px;height:14px;border-radius:50%;background:var(--slate)}
  .header-brand{left:89px;top:36px}
  .phone{right:89px;top:20px;color:var(--slate);font-size:19px;display:flex;align-items:center;gap:10px}
  .main-nav{top:69px;left:0;width:1200px;height:22px}
  .main-nav a{position:absolute;color:var(--nav-text);text-decoration:none;font-size:15px;letter-spacing:.5px}

  /* hero */
  .hero{left:0;top:108px;width:1200px;height:640px;overflow:hidden;
    background:radial-gradient(ellipse at 30% 55%,#3a2a6a 0%,#1c1740 35%,#0a0a1e 65%),#0a0a1e}
  .hero::after{content:"";position:absolute;right:0;top:0;width:420px;height:640px;
    background:linear-gradient(90deg,rgba(0,0,0,0),rgba(110,60,30,.55))}
  .hero-title{left:89px;top:170px;font-family:var(--serif);font-weight:600;font-size:76px;line-height:.92;letter-spacing:2px;z-index:2}
  .hero-sub{left:91px;top:332px;font-size:20px;line-height:33px;z-index:2}
  .btn{display:flex;align-items:center;justify-content:center;background:var(--slate);color:var(--white);font-size:16px;font-weight:600;letter-spacing:.5px}
  .hero-btn{left:91px;top:418px;width:195px;height:44px;z-index:2}
  .hero-photo{left:599px;top:63px;width:514px;height:514px;border-radius:50%;border:6px solid var(--slate-light);z-index:2;
    background:radial-gradient(circle at 50% 45%,#cfcfcf,#5a5a5a 55%,#111 95%)}
  .hero-wave{left:0;top:580px;z-index:3}

  /* section heads */
  .section-title{font-family:var(--serif);font-weight:600;font-size:46px;letter-spacing:3px;line-height:1}
  .rule{height:4px;width:36px;background:var(--slate)}
  .center{text-align:center;width:1200px;left:0}

  /* bio */
  .bio-photo{left:91px;top:835px;width:514px;height:514px;border-radius:50%;border:6px solid var(--slate-light);
    background:radial-gradient(ellipse at 50% 45%,#f2a03a,#c24a10 35%,#3a1206 70%,#0a0403)}
  .bio-text{left:686px;top:967px;width:422px;font-size:15px;line-height:33.2px;text-align:justify}

  /* discography */
  .album-photo{background:linear-gradient(135deg,#b09770,#8a7350 55%,#6b7a52)}
  .album-circle{border-radius:50%;background:var(--slate);display:flex;align-items:center;justify-content:center;text-align:center;
    font-family:var(--serif);font-weight:700;font-size:50px;line-height:58px;color:var(--white)}
  .storm-art{background:linear-gradient(180deg,#4d4a5c 0%,#2e2b3a 45%,#8a3a14 78%,#1a1410 100%)}

  /* cd */
  .cd-text{left:89px;top:2748px;width:421px;font-size:15px;line-height:33.2px}

  /* gallery */
  .tile{overflow:hidden}
  .play{position:absolute;left:50%;top:50%;transform:translate(-50%,-50%)}

  /* footer */
  .site-footer{left:0;top:3938px;width:1200px;height:470px;background:var(--footer)}
  .footer-head{font-family:var(--serif);font-weight:600;font-size:30px;letter-spacing:2px}
  .footer-list{list-style:none;font-size:15px;line-height:30.8px}
  .social{left:133px;top:4133px;display:flex;gap:24px}
  .social span{display:block;width:14px;height:14px;border-radius:50%;background:var(--white)}
  .email{left:835px;top:4110px;width:274px;height:38px;background:var(--white);color:#999;font-size:14px;padding:10px 14px}
  .subscribe{left:835px;top:4155px;width:274px;height:39px}
  .copyright{top:4364px;font-size:13px}
</style>
</head>
<body>

<header class="abs site-header">
  <div class="abs brand header-brand"><span class="brand-dot"></span>Rosko Tamblin</div>
  <div class="abs phone">
    <svg width="16" height="16" viewBox="0 0 24 24" aria-hidden="true"><path fill="#6b7590" d="M6.6 10.8a15 15 0 0 0 6.6 6.6l2.2-2.2a1 1 0 0 1 1-.25 11.4 11.4 0 0 0 3.6.57 1 1 0 0 1 1 1V20a1 1 0 0 1-1 1A17 17 0 0 1 3 4a1 1 0 0 1 1-1h3.5a1 1 0 0 1 1 1c0 1.25.2 2.45.57 3.57a1 1 0 0 1-.25 1z"/></svg>
    +8 888 888 888
  </div>
  <nav class="abs main-nav">
    <a style="left:445px">HOME</a>
    <a style="left:536px">BIO</a>
    <a style="left:608px">DISCOGRAPHY</a>
    <a style="left:764px">CD COVERS</a>
    <a style="left:895px">GALLERY</a>
    <a style="left:1008px">CONTACT US</a>
  </nav>
</header>

<section class="abs hero">
  <h1 class="abs hero-title">ROSKO<br>TAMBLIN</h1>
  <p class="abs hero-sub">LOREM IPSUM DOLOR SIT AMET, CONSECTETUR<br>ADIPISCING ELIT, SED DO EIUSMOD</p>
  <div class="abs btn hero-btn">GET STARTED</div>
  <div class="abs hero-photo" role="img" aria-label="Black and white portrait of the songwriter in a hat playing a mandolin"></div>
  <svg class="abs hero-wave" width="1200" height="60" viewBox="0 0 1200 60" aria-hidden="true">
    <path d="M0 25 C300 38 700 30 1200 8 L1200 60 L0 60 Z" fill="#8a93ab"/>
    <path d="M0 40 C300 48 700 42 1200 22 L1200 60 L0 60 Z" fill="#000"/>
  </svg>
</section>

<section>
  <div class="abs bio-photo" role="img" aria-label="The songwriter standing in front of a glowing fire crater at night"></div>
  <h2 class="abs section-title" style="left:686px;top:866px">BIO</h2>
  <div class="abs rule" style="left:686px;top:929px"></div>
  <p class="abs bio-text">Rosko Tamblin was born and raised in Houston, Texas. He began playing music at the age of eight when his sister returned home from summer camp and asked her parents to buy her a baritone ukulele. She taught her younger brother some chords on the ukulele and he was hooked. The following spring, they went to one of the border towns in Mexico and bought a Mexican guitar for $12. They restrung it with nylon strings and Tamblin began to learn how to play the guitar.</p>
  <div class="abs btn" style="left:686px;top:1263px;width:158px;height:48px;font-size:15px">READ MORE</div>
</section>

<section>
  <h2 class="abs section-title center" style="top:1455px">DISCOGRAPHY</h2>
  <div class="abs rule" style="left:582px;top:1516px"></div>

  <div class="abs album-photo" style="left:577px;top:1553px;width:623px;height:472px" role="img" aria-label="Smiling songwriter in a white shirt before a clay wall"></div>
  <div class="abs album-circle" style="left:310px;top:1592px;width:394px;height:394px">CHART OF<br>TOMORROW</div>

  <div class="abs storm-art" style="left:0;top:2054px;width:623px;height:473px" role="img" aria-label="Album art with a stormy sky, lightning, burning city and a silhouetted figure"></div>
  <div class="abs album-circle" style="left:488px;top:2094px;width:394px;height:394px">RESTLESS<br>SEASONS</div>
</section>

<section>
  <h2 class="abs section-title" style="left:89px;top:2650px">CD COVERS</h2>
  <div class="abs rule" style="left:89px;top:2710px"></div>
  <p class="abs cd-text">Lorem ipsum dolor sit amet, consectetur adipiscing elit, sed do eiusmod tempor incididunt ut labore et dolore magna aliqua. Ut enim ad minim veniam, quis nostrud exercitation ullamco laboris nisi ut aliquip ex ea commodo consequat. Duis aute irure dolor in reprehenderit in voluptate velit esse cillum dolore eu fugiat nulla pariatur.</p>
  <div class="abs btn" style="left:89px;top:2975px;width:156px;height:48px;font-size:15px">WATCH NOW</div>
  <svg class="abs" style="left:550px;top:2640px" width="570" height="395" viewBox="0 0 570 395" role="img" aria-label="Music album sleeve with a partly pulled out disc">
    <defs>
      <radialGradient id="disc" cx="50%" cy="50%" r="50%">
        <stop offset="0" stop-color="#3a3f55"/><stop offset=".85" stop-color="#1c2030"/><stop offset="1" stop-color="#c9ccd6"/>
      </radialGradient>
      <linearGradient id="sleeve" x1="0" y1="0" x2="1" y2="1">
        <stop offset="0" stop-color="#3a2a48"/><stop offset="1" stop-color="#1e1628"/>
      </linearGradient>
    </defs>
    <circle cx="382" cy="198" r="188" fill="url(#disc)"/>
    <rect x="0" y="0" width="397" height="395" fill="url(#sleeve)"/>
    <circle cx="210" cy="205" r="115" fill="#4a4a8a" opacity=".6"/>
  </svg>
</section>

<section>
  <h2 class="abs section-title center" style="top:3146px">PICTURES</h2>
  <div class="abs rule" style="left:582px;top:3208px"></div>

  <div class="abs tile" style="left:89px;top:3251px;width:455px;height:281px;background:radial-gradient(circle at 50% 45%,#bdbdbd,#444 60%,#111)" role="img" aria-label="Video still of the songwriter playing mandolin">
    <svg class="play" width="56" height="56" viewBox="0 0 56 56" aria-hidden="true"><circle cx="28" cy="28" r="26" fill="rgba(255,255,255,.35)" stroke="#fff" stroke-width="2"/><path d="M22 17 L39 28 L22 39 Z" fill="#fff"/></svg>
  </div>
  <div class="abs tile" style="left:555px;top:3251px;width:272px;height:281px;background:linear-gradient(180deg,#9fb08a,#d9d2c0 60%,#eeeeee)" role="img" aria-label="Songwriter in a straw cowboy hat outdoors"></div>
  <div class="abs tile" style="left:837px;top:3251px;width:274px;height:281px;background:linear-gradient(135deg,#c8451a,#e39a2e 40%,#7a8a5a 75%,#3a4a2a)" role="img" aria-label="Album cover art with flames and a coffee cup on a table"></div>
  <div class="abs tile" style="left:89px;top:3544px;width:272px;height:281px;background:linear-gradient(160deg,#5a6e72,#2e3e44 55%,#c8d2d4)" role="img" aria-label="Waves crashing on a rocky shore"></div>
  <div class="abs tile" style="left:371px;top:3544px;width:274px;height:281px;background:radial-gradient(circle at 45% 55%,#d9c23a,#c83a8a 45%,#6a2a9a 80%)" role="img" aria-label="Colorful album cover of a musician holding a mandolin"></div>
  <div class="abs tile" style="left:656px;top:3544px;width:455px;height:281px;background:linear-gradient(135deg,#b08a5a,#3a4a5a 55%,#1a2430)" role="img" aria-label="Video still of headphones resting on a laptop keyboard">
    <svg class="play" width="56" height="56" viewBox="0 0 56 56" aria-hidden="true"><circle cx="28" cy="28" r="26" fill="rgba(255,255,255,.35)" stroke="#fff" stroke-width="2"/><path d="M22 17 L39 28 L22 39 Z" fill="#fff"/></svg>
  </div>
</section>

<footer class="abs site-footer">
  <div class="abs brand" style="left:89px;top:100px;color:#8a93ab"><span class="brand-dot" style="background:#8a93ab"></span>Rosko Tamblin</div>
  <div class="abs social" style="top:195px" aria-label="Social links"><span></span><span></span><span></span><span></span></div>

  <h3 class="abs footer-head" style="left:413px;top:100px">LINKS</h3>
  <ul class="abs footer-list" style="left:413px;top:157px">
    <li>Home</li><li>Bio</li><li>Discography</li><li>CD covers</li><li>Gallery</li><li>Contact Us</li>
  </ul>

  <h3 class="abs footer-head" style="left:601px;top:100px">OTHERS</h3>
  <ul class="abs footer-list" style="left:601px;top:157px">
    <li>FAQ</li><li>Terms &amp; Conditions</li><li>Privacy Policy</li>
  </ul>

  <h3 class="abs footer-head" style="left:834px;top:100px">NEWSLETTER</h3>
  <div class="abs email" style="top:172px">Your Email Address</div>
  <div class="abs btn subscribe" style="top:217px">SUBSCRIBE</div>

  <p class="abs copyright center" style="top:426px">The Company Name © 2020. All Rights Reserved.</p>
</footer>

</body>
</html>
```